Professional & attention grabbing.

A business card design, front and back. I already have a logo I will attach, but I am open to something new as well.
Things to include:
Name:
Title:
Phone:
Email:
Wanting something that is professional but attention grabbing.
Also we do a lot of work using drones on natural gas pipelines (leading the future)if you want to include any of that. I'm open to ideas.
Target Market(s)
Natural gas transmission industry / greenhouse gas mitigation industry
Industry/Entity Type
Business
Colors
Designer to choose colors to be used in the design.
Look and feel
Each slider illustrates characteristics of the customer's brand and the style your logo design should communicate.

```html
<!DOCTYPE html>
<html lang="en">
<head>
<meta charset="utf-8">
<title>Crestline Inspections – Business Card</title>
<link rel="stylesheet" href="https://fonts.googleapis.com/css2?family=Roboto+Condensed:wght@400;700&display=swap">
<style>
  :root {
    --canvas: #e9e7e4;
    --card-white: #ffffff;
    --brand-red: #c8202a;
    --brand-red-deep: #a8161f;
    --swoosh-grey: #3a3a3c;
    --ink-grey: #4a4a4c;
    --text-light: #ffffff;
  }
  * { box-sizing: border-box; margin: 0; padding: 0; }
  html, body { width: 1200px; height: 950px; overflow: hidden; }
  body {
    background: var(--canvas);
    font-family: "Roboto Condensed", Arial, sans-serif;
    position: relative;
  }
  .card {
    position: absolute;
    width: 720px;
    height: 410px;
    border-radius: 22px;
    overflow: hidden;
    box-shadow: 0 10px 28px rgba(0,0,0,0.18);
  }
  .card--front { left: 60px; top: 50px; background: var(--card-white); }
  .card--back {
    left: 420px; top: 500px;
    background: var(--brand-red);
  }
  .front-shape { position: absolute; inset: 0; width: 100%; height: 100%; }

  .brand {
    position: absolute;
    left: 70px; top: 150px;
    display: flex; align-items: center; gap: 16px;
  }
  .brand__square { width: 40px; height: 40px; background: var(--brand-red); }
  .brand__name {
    font-weight: 700;
    font-size: 46px;
    letter-spacing: 1px;
    color: var(--ink-grey);
    text-transform: uppercase;
  }

  .contact {
    position: absolute;
    right: 40px; bottom: 46px;
    color: var(--text-light);
    text-align: right;
    white-space: nowrap;
  }
  .contact__name {
    font-weight: 700;
    font-size: 23px;
    letter-spacing: 0.5px;
    text-transform: uppercase;
  }
  .contact__title { font-weight: 400; text-transform: none; }
  .contact__details {
    margin-top: 10px;
    font-size: 16px;
    letter-spacing: 0.3px;
  }
  .contact__sep { margin: 0 7px; opacity: 0.8; }

  .back-pattern {
    position: absolute; inset: 0;
    background: linear-gradient(135deg, var(--brand-red) 0%, var(--brand-red-deep) 100%);
  }
  .back-brand {
    position: absolute; inset: 0;
    display: flex; flex-direction: column;
    align-items: center; justify-content: center;
    color: var(--text-light);
  }
  .back-brand__name {
    font-weight: 700;
    font-size: 64px;
    letter-spacing: 2px;
    text-transform: uppercase;
  }
  .back-brand__web {
    margin-top: 10px;
    font-size: 18px;
    letter-spacing: 4px;
  }
</style>
</head>
<body>

  <section class="card card--front" aria-label="Business card front">
    <svg class="front-shape" viewBox="0 0 720 410" preserveAspectRatio="none" aria-hidden="true">
      <path d="M560 0 C 520 160, 360 300, 230 410 L 720 410 L 720 0 Z" fill="var(--brand-red)"/>
      <path d="M548 0 C 505 150, 345 290, 212 410 L 230 410 C 360 300, 520 160, 560 0 Z" fill="var(--swoosh-grey)"/>
    </svg>

    <div class="brand">
      <span class="brand__square"></span>
      <span class="brand__name">Crestline</span>
    </div>

    <div class="contact">
      <p class="contact__name">Dana Whitlow - <span class="contact__title">CEO/Founder</span></p>
      <p class="contact__details">
        555 014 2287<span class="contact__sep">|</span>dana@crestline.co<span class="contact__sep">|</span>www.crestline.co
      </p>
    </div>
  </section>

  <section class="card card--back" aria-label="Business card back">
    <div class="back-pattern" role="img" aria-label="Repeating brand pattern in tonal red"></div>
    <div class="back-brand">
      <p class="back-brand__name">Crestline</p>
      <p class="back-brand__web">www.crestline.co</p>
    </div>
  </section>

</body>
</html>
```